Bright Harbor Brochure/Flyer Revisions

Improve the current design and over all look for Tri-Fold brochure and 8 x 11 flyer along with update the text and view picture substitutions.

Target Market(s)

Currently our brochure is geared more towards the Cancer Patient, and less Senior.
I want to take the new revisions text, or new message, and incorporate it into the new designed brochure and flyer. I want a nice picture of a senior or couple to be primary view shot and the cancer patients secondary.
Please visit our website; www.brightharbors-demo.org

Requirements
Must have
• we want all Seniors and Cancer Patients that own a life insurance policy, group or individual to call us. We want the consumer to be educated and know their rights.
Bright Harbors will be there ADVOCATE and Financial RESOURCE

```html
<!DOCTYPE html>
<html lang="en">
<head>
<meta charset="utf-8">
<title>Bright Harbors Tri-Fold Brochure</title>
<link rel="stylesheet" href="https://fonts.googleapis.com/css2?family=Bitter:wght@400;600&family=Open+Sans:wght@400;600;700&display=swap">
<style>
  :root {
    --pink: #ef6aa6;
    --pink-soft: #f8d7e6;
    --blue: #3f6fb2;
    --orange: #f4a11d;
    --ink: #4a4a4a;
    --ink-dark: #3a3a3a;
    --rule: #bdbdbd;
    --swoosh: #545454;
    --page: #e4e5e7;
    --paper: #ffffff;
  }
  * { box-sizing: border-box; margin: 0; padding: 0; }
  html, body { width: 1200px; height: 945px; overflow: hidden; background: var(--page); }
  body { position: relative; font-family: "Open Sans", Arial, sans-serif; color: var(--ink); }

  .brochure {
    position: absolute; left: 39px; top: 41px; width: 1118px; height: 866px;
    background: var(--paper); display: flex;
    box-shadow: 0 2px 8px rgba(0,0,0,.18);
  }
  .panel { position: relative; height: 100%; overflow: hidden; }
  .panel + .panel { border-left: 1px solid #cfcfcf; }
  .panel--reply { width: 373px; }
  .panel--benefits { width: 372px; }
  .panel--cover { width: 373px; }
  .panel-art { position: absolute; inset: 0; width: 100%; height: 100%; }

  .abs { position: absolute; }
  .center { left: 0; right: 0; text-align: center; }
  .brand-name {
    font-family: "Open Sans", Arial, sans-serif; font-weight: 600;
    color: var(--blue); font-size: 34px; letter-spacing: 1px; line-height: 1;
  }

  /* Reply panel */
  .reply-frame {
    position: absolute; inset: 5px; border: 5px solid var(--pink-soft); border-radius: 12px;
  }
  .reply-lead { top: 138px; font-size: 15px; color: var(--ink-dark); }
  .call-label { top: 166px; font-size: 21px; color: var(--orange); }
  .phone { top: 188px; font-size: 49px; font-weight: 700; color: var(--pink); letter-spacing: -0.5px; }
  .confidential-a { top: 250px; font-size: 16px; color: var(--ink); }
  .confidential-b { top: 272px; font-size: 20px; font-weight: 700; color: var(--ink); }
  .reply-rule { position: absolute; left: 34px; width: 301px; top: 318px; border-top: 1px solid var(--rule); }

  .vertical { writing-mode: vertical-rl; }
  .mailer-title {
    left: 271px; top: 355px; width: 56px; height: 212px;
    font-size: 21px; font-weight: 700; color: var(--ink-dark); line-height: 1.25; text-align: center;
  }
  .brm-box {
    left: 153px; top: 333px; width: 59px; height: 338px; background: var(--pink); color: #fff;
    padding: 6px 4px; display: flex; flex-direction: column; align-items: center; justify-content: center;
  }
  .brm-box .brm-title { font-size: 22px; font-weight: 700; letter-spacing: .5px; line-height: 1.2; }
  .brm-box .brm-permit { font-size: 10px; line-height: 1.3; white-space: nowrap; }
  .brm-permit .gap { display: inline-block; height: 18px; }
  .postage-note { left: 128px; top: 344px; width: 14px; font-size: 10px; color: var(--ink-dark); }
  .mail-address {
    left: 33px; top: 383px; width: 76px; font-size: 17px; line-height: 1.35; color: var(--ink-dark);
    font-style: normal;
  }
  .mail-address strong { font-weight: 700; }
  .no-postage {
    left: 225px; top: 701px; width: 107px; height: 140px; border: 1px solid var(--blue);
    color: var(--blue); font-size: 12px; line-height: 1.35; text-align: center;
    display: flex; align-items: center; justify-content: center;
  }

  /* Benefits panel */
  .section-kicker { right: 8px; top: 350px; font-family: "Bitter", Georgia, serif; font-size: 27px; color: var(--pink); }
  .section-title { right: 8px; top: 384px; font-family: "Bitter", Georgia, serif; font-size: 25px; color: var(--ink); }
  .section-rule { position: absolute; left: 112px; right: 0; top: 419px; border-top: 1px solid var(--rule); }
  .benefits-intro { left: 52px; right: 16px; top: 440px; font-size: 15px; line-height: 1.4; color: var(--blue); }
  .benefits-intro strong { color: var(--pink); font-weight: 700; }
  .benefit-list {
    position: absolute; left: 34px; top: 513px; list-style: none;
    font-size: 14px; line-height: 20.4px; color: var(--ink);
  }
  .benefit-list li { padding-left: 14px; position: relative; }
  .benefit-list li::before {
    content: ""; position: absolute; left: 0; top: 7px; width: 7px; height: 7px;
    border: 1.3px solid var(--ink); border-radius: 50%;
  }

  /* Cover panel */
  .cover-brand { top: 77px; }
  .cover-rule { position: absolute; left: 29px; width: 301px; top: 162px; border-top: 1px solid var(--rule); }
  .cover-headline { left: 31px; top: 176px; font-family: "Bitter", Georgia, serif; font-weight: 400; line-height: 1; }
  .cover-headline .kicker { display: block; font-size: 26px; color: var(--pink); letter-spacing: 1px; }
  .cover-headline .line { display: block; font-size: 34px; color: var(--blue); letter-spacing: 1px; margin-top: 10px; }
  .cover-url { top: 826px; font-size: 20px; color: var(--ink); }
  .cover-url span { color: var(--pink); }
</style>
</head>
<body>
<main class="brochure">

  <section class="panel panel--reply">
    <div class="reply-frame"></div>
    <div class="abs center brand-name" style="top:74px;">Bright Harbors</div>
    <p class="abs center reply-lead">Return the attached post card or</p>
    <p class="abs center call-label">Call Toll Free</p>
    <p class="abs center phone">800-555-0147</p>
    <p class="abs center confidential-a">All Communication will be</p>
    <p class="abs center confidential-b">Kept Strictly Confidential!</p>
    <div class="reply-rule"></div>

    <h3 class="abs vertical mailer-title">RAISING<br>QUALITY OF LIFE</h3>
    <svg class="abs" style="left:262px;top:595px" width="68" height="56" viewBox="0 0 68 56" aria-hidden="true">
      <g fill="var(--pink)">
        <rect x="0" y="0" width="68" height="3"/><rect x="0" y="13" width="68" height="3"/>
        <rect x="0" y="26" width="68" height="3"/><rect x="0" y="39" width="68" height="3"/>
        <rect x="0" y="52" width="68" height="3"/>
      </g>
    </svg>

    <div class="abs vertical brm-box">
      <span class="brm-title">BUSINESS REPLY MAIL</span>
      <span class="brm-permit">First-Class Mail<span class="gap"></span>Permit No. 1042<span class="gap"></span>MARLOW, GA</span>
    </div>
    <p class="abs vertical postage-note">POSTAGE WILL BE PAID BY ADDRESSEE</p>
    <address class="abs vertical mail-address">
      <strong>BRIGHT HARBORS</strong><br>4410 Lakeside PKWY STE 210<br>MARLOW GA 30555-0100
    </address>

    <svg class="abs" style="left:125px;top:698px" width="84" height="138" viewBox="0 0 84 138" aria-hidden="true">
      <g fill="var(--blue)">
        <rect x="0" y="0" width="8" height="138"/><rect x="19" y="0" width="8" height="138"/>
        <rect x="38" y="0" width="8" height="138"/><rect x="57" y="0" width="8" height="138"/>
        <rect x="76" y="0" width="8" height="138"/>
      </g>
    </svg>
    <div class="abs vertical no-postage">NO POSTAGE<br>NECESSARY<br>IF MAILED<br>IN THE<br>UNITED STATES</div>
  </section>

  <section class="panel panel--benefits">
    <svg class="panel-art" viewBox="0 0 334 775" preserveAspectRatio="none">
      <defs>
        <linearGradient id="hospitalTone" x1="0" y1="0" x2="1" y2="1">
          <stop offset="0" stop-color="#eef1f4"/>
          <stop offset=".55" stop-color="#d9e2ea"/>
          <stop offset="1" stop-color="#b9c6d2"/>
        </linearGradient>
      </defs>
      <path role="img" aria-label="Photo: smiling patient in a head scarf seated in a bright hospital corridor"
            d="M0,0 H30 C178,60 178,250 0,318 Z" fill="url(#hospitalTone)"/>
      <path d="M30,0 H78 C228,62 226,300 0,400 L0,318 C178,250 178,60 30,0 Z" fill="var(--swoosh)"/>
      <path d="M0,318 Q82,300 152,252 Q88,304 0,309 Z" fill="var(--pink)"/>
      <path d="M0,414 Q42,400 72,392 Q36,399 0,404 Z" fill="var(--pink)"/>
    </svg>

    <p class="abs section-kicker">RAISING</p>
    <p class="abs section-title">QUALITY OF LIFE</p>
    <div class="section-rule"></div>
    <p class="abs benefits-intro">Own a life insurance policy? With<br><strong>BRIGHT HARBOR</strong> as your advocate and<br>financial resource, you can...</p>
    <ul class="benefit-list">
      <li>Reduce financial stress</li>
      <li>Pay for uninsured healthcare costs</li>
      <li>Pay for alternative treatment</li>
      <li>Improve quality of life</li>
      <li>Pay off debt</li>
      <li>Take a vacation or dream trip</li>
      <li>Make cash gifts to family and friends</li>
      <li>Fulfill life wishes</li>
      <li>Pay for college funding</li>
      <li>Make home improvements</li>
      <li>Donate to church or charity</li>
      <li>See the money enjoyed by relatives now</li>
      <li>Invest in financial opportunities</li>
      <li>Buy a new car</li>
      <li>Fund long term care expenses</li>
      <li>Plan ahead for final estate needs</li>
    </ul>
  </section>

  <section class="panel panel--cover">
    <svg class="panel-art" viewBox="0 0 334 775" preserveAspectRatio="none">
      <defs>
        <linearGradient id="beachTone" x1="0" y1="0" x2="1" y2="1">
          <stop offset="0" stop-color="#dfe6ea"/>
          <stop offset=".5" stop-color="#e9e2d6"/>
          <stop offset="1" stop-color="#cdbfa8"/>
        </linearGradient>
      </defs>
      <path role="img" aria-label="Photo: happy senior couple embracing on a beach"
            d="M334,308 C200,330 30,430 20,560 C30,650 150,695 334,698 Z" fill="url(#beachTone)"/>
      <path d="M334,225 C180,262 5,400 10,560 C15,680 150,726 334,726 L334,698 C150,695 30,650 20,560 C30,430 200,330 334,308 Z" fill="var(--pink)"/>
      <path d="M118,680 Q220,698 334,686 L334,693 Q220,706 118,680 Z" fill="var(--swoosh)"/>
    </svg>

    <div class="abs center brand-name cover-brand">Bright Harbors</div>
    <div class="cover-rule"></div>
    <h1 class="abs cover-headline">
      <span class="kicker">DISCOVER</span>
      <span class="line">FINANCIAL</span>
      <span class="line" style="margin-top:8px;">FREEDOM</span>
    </h1>
    <p class="abs center cover-url">www.<span>brightharbors-demo</span>.org</p>
  </section>

</main>
</body>
</html>
```